Up to the Challenge - PPT Template with Splash Slide

We are looking for a PPT template that has 4 slides.
1. Splash slide (Creative, fun, no content, a visual representation of the theme)
2. Section header slide
3. Content Slide
4. Content Slide, another design option
The theme is 'UP to the Challenge'. The design should reflect this theme.
The colors should be in Purple (#864B99), Blue (#0A80C2), and Green (#52B054).

```html
<!DOCTYPE html>
<html lang="en">
<head>
<meta charset="utf-8">
<title>Up to the Challenge – Presentation Theme</title>
<link rel="stylesheet" href="https://fonts.googleapis.com/css2?family=Montserrat:wght@400&family=Open+Sans:wght@300;400;700&display=swap">
<style>
  :root {
    --purple: #864B99;
    --blue: #0A80C2;
    --green: #52B054;
    --navy: #2c3a63;
    --ink: #111111;
    --paper: #f5f5f5;
    --band-dark: #4a4a4a;
    --muted: #8a8a8a;
  }
  * { margin: 0; padding: 0; box-sizing: border-box; }
  html, body { width: 1200px; height: 867px; overflow: hidden; }
  body {
    position: relative;
    background: linear-gradient(100deg, #a3a3a3 0%, #7c7c7c 45%, #5e5e5e 100%);
    font-family: "Open Sans", Arial, sans-serif;
    color: var(--ink);
  }
  .board-title {
    position: absolute; left: 0; top: 46px; width: 585px; height: 91px;
    background: var(--band-dark);
    padding: 21px 0 0 46px;
    font-family: "Montserrat", Arial, sans-serif;
    color: #fff; font-size: 20px; line-height: 26px; letter-spacing: 0.2px;
  }
  .option-label {
    position: absolute; right: 45px; top: 82px;
    font-family: "Montserrat", Arial, sans-serif; color: #fff; font-size: 16px;
  }
  .slide {
    position: absolute; width: 538px; height: 303px;
    background: var(--paper); overflow: hidden;
    box-shadow: 0 6px 14px rgba(0,0,0,0.35);
  }
  .slide svg.art { position: absolute; left: 0; top: 0; width: 538px; height: 303px; }
  .splash { left: 47px; top: 185px; }
  .section { left: 615px; top: 185px; }
  .content-a { left: 47px; top: 520px; }
  .content-b { left: 615px; top: 520px; }

  .section-title {
    position: absolute; left: 25px; top: 105px;
    color: #fff; font-weight: 300; font-size: 26px; line-height: 23px; letter-spacing: 0.3px;
  }
  .footer-url { position: absolute; font-size: 5px; color: #555; white-space: nowrap; }
  .footer-rule { position: absolute; height: 1px; background: #d6d6d6; }
  .page-num {
    position: absolute; width: 11px; height: 11px; background: var(--blue);
    transform: rotate(45deg) scaleY(0.7);
  }
  .page-num span {
    display: block; transform: rotate(-45deg); color: #fff; font-size: 4px;
    text-align: center; line-height: 11px;
  }
  .slide-heading {
    position: absolute; left: 20px; top: 17px;
    color: #fff; font-size: 17px; font-weight: 400; letter-spacing: 0.2px;
  }
  .slide-heading strong { font-weight: 700; }
  .lead { position: absolute; font-weight: 700; font-size: 11px; line-height: 12.7px; }
  .lead-wide { font-size: 12.2px; line-height: 13.8px; }
  .body-small { position: absolute; font-size: 8.3px; line-height: 11.6px; }
  .body-large { position: absolute; font-size: 11.2px; line-height: 12.8px; }
  .divider-green {
    position: absolute; left: 296px; top: 79px; width: 2px; height: 187px; background: var(--green);
  }
  .accent-purple {
    position: absolute; left: 18px; top: 75px; width: 3px; height: 51px; background: var(--purple);
  }
  .bullets { position: absolute; list-style: none; font-size: 11.5px; line-height: 16.1px; white-space: nowrap; }
  .bullets li::before { content: "•"; margin-right: 4px; }
</style>
</head>
<body>

<header class="board-title">UP TO THE CHALLENGE<br>POWER POINT TEMPLATE DESIGN THEME</header>
<div class="option-label">OPTION 1</div>

<!-- Splash slide -->
<section class="slide splash">
  <svg class="art" viewBox="0 0 538 303">
    <defs>
      <linearGradient id="splashBg" x1="0" y1="0" x2="1" y2="0">
        <stop offset="0" stop-color="#d9d9d9"/><stop offset="1" stop-color="#ffffff"/>
      </linearGradient>
      <linearGradient id="sunsetPhoto" x1="0" y1="0" x2="1" y2="1">
        <stop offset="0" stop-color="#c9a58a"/><stop offset="0.45" stop-color="#f2b04a"/>
        <stop offset="0.75" stop-color="#b0573a"/><stop offset="1" stop-color="#4e2b28"/>
      </linearGradient>
      <linearGradient id="shardsSplash" x1="0" y1="0" x2="1" y2="1">
        <stop offset="0" stop-color="#864B99" stop-opacity="0.85"/>
        <stop offset="0.5" stop-color="#52B054" stop-opacity="0.8"/>
        <stop offset="1" stop-color="#0A80C2" stop-opacity="0.85"/>
      </linearGradient>
    </defs>
    <rect width="538" height="303" fill="url(#splashBg)"/>
    <polygon points="270,0 345,0 470,152 345,303 278,303 395,152" fill="var(--blue)"/>
    <polygon points="0,0 262,0 385,152 270,303 0,303" fill="url(#sunsetPhoto)" role="img" aria-label="Photo: person leaping between mountain cliffs at sunset"/>
    <polygon points="270,10 440,10 538,130 538,250 440,290 300,260 160,190 320,85" fill="url(#shardsSplash)" role="img" aria-label="Artwork: cluster of overlapping purple, green and blue triangles"/>
  </svg>
</section>

<!-- Section header slide -->
<section class="slide section">
  <svg class="art" viewBox="0 0 538 303">
    <defs>
      <linearGradient id="shardsSection" x1="0" y1="0" x2="1" y2="1">
        <stop offset="0" stop-color="#0A80C2" stop-opacity="0.75"/>
        <stop offset="0.5" stop-color="#52B054" stop-opacity="0.7"/>
        <stop offset="1" stop-color="#864B99" stop-opacity="0.8"/>
      </linearGradient>
      <linearGradient id="navyPhoto" x1="0" y1="0" x2="1" y2="0">
        <stop offset="0" stop-color="#28355c"/><stop offset="1" stop-color="#46557e"/>
      </linearGradient>
    </defs>
    <polygon points="0,82 236,82 326,181 0,181" fill="var(--blue)"/>
    <polygon points="0,181 326,181 337,193 0,193" fill="var(--green)"/>
    <polygon points="326,181 538,181 538,280 416,280" fill="url(#navyPhoto)" role="img" aria-label="Photo: businessman stepping up a rising arrow drawn by a hand"/>
    <polygon points="325,100 445,33 512,120 460,164 380,150" fill="url(#shardsSection)" role="img" aria-label="Artwork: cluster of overlapping blue, green and purple triangles"/>
  </svg>
  <h1 class="section-title">SECTION HEADER<br>CHALLENGE 1</h1>
  <div class="footer-url" style="left:24px; top:287px;">www.yourwebsite.com</div>
</section>

<!-- Content slide A -->
<section class="slide content-a">
  <svg class="art" viewBox="0 0 538 303">
    <defs>
      <linearGradient id="shardsSmallA" x1="0" y1="0" x2="1" y2="1">
        <stop offset="0" stop-color="#0A80C2" stop-opacity="0.75"/>
        <stop offset="0.5" stop-color="#52B054" stop-opacity="0.7"/>
        <stop offset="1" stop-color="#864B99" stop-opacity="0.85"/>
      </linearGradient>
    </defs>
    <polygon points="0,0 321,0 366,50 0,50" fill="var(--purple)"/>
    <polygon points="0,50 366,50 371,55 0,55" fill="var(--blue)"/>
    <polygon points="366,50 538,50 538,64 379,64" fill="var(--green)"/>
    <polygon points="418,52 490,12 526,60 495,88 450,78" fill="url(#shardsSmallA)" role="img" aria-label="Artwork: small cluster of overlapping triangles"/>
  </svg>
  <h2 class="slide-heading"><strong>ABOUT</strong> THE CHALLENGE</h2>
  <p class="lead" style="left:17px; top:73px; width:215px;">Lorem ipsum dolor sit amet,<br>consectetuer adipiscing elit, sed diam nonummy nibh euismod tincidunt ut laoreet dolore magna aliquam erat volutpat. Ut wisi enim ad minim veniam,</p>
  <p class="body-small" style="left:17px; top:160px; width:255px;">Lorem ipsum dolor sit amet, consectetuer adipiscing elit, sed diam nonummy nibh euismod tincidunt ut laoreet dolore magna aliquam erat volutpat. Ut wisi enim ad minim veniam, Lorem ipsum dolor sit amet, Lorem ipsum dolor sit amet, consectetuer adipiscing elit, sed diam nonummy nibh euismod tincidunt ut laoreet dolore magna aliquam erat volutpat. Ut wisi enim ad minim veniam, quis nostrud exerci tation ullamcorper suscipit lobortis nisl ut aliquip ex ea</p>
  <div class="divider-green"></div>
  <p class="body-large" style="left:322px; top:117px; width:198px;">Lorem ipsum dolor sit amet, consectetuer adipiscing elit, sed diam nonummy nibh euismod tincidunt ut laoreet dolore magna aliquam erat volutpat. Ut wisi enim ad minim veniam, Lorem ipsum dolor sit amet, Lorem ipsum dolor sit amet, consectetuer adipiscing elit, sed diam nonummy nibh euismod tincidunt ut laoreet dolore magna aliquam erat</p>
  <div class="footer-url" style="left:19px; top:283px;">www.yourwebsite.com</div>
  <div class="footer-rule" style="left:66px; top:286px; width:430px;"></div>
  <div class="page-num" style="left:507px; top:281px;"><span>1</span></div>
</section>

<!-- Content slide B -->
<section class="slide content-b">
  <svg class="art" viewBox="0 0 538 303">
    <defs>
      <linearGradient id="purpleFade" x1="0" y1="0" x2="1" y2="0">
        <stop offset="0" stop-color="#864B99"/><stop offset="1" stop-color="#864B99" stop-opacity="0.2"/>
      </linearGradient>
      <linearGradient id="shardsSmallB" x1="0" y1="0" x2="1" y2="1">
        <stop offset="0" stop-color="#0A80C2" stop-opacity="0.75"/>
        <stop offset="0.5" stop-color="#52B054" stop-opacity="0.7"/>
        <stop offset="1" stop-color="#864B99" stop-opacity="0.85"/>
      </linearGradient>
      <radialGradient id="climberPhoto" cx="0.5" cy="0.55" r="0.6">
        <stop offset="0" stop-color="#ffd24a"/><stop offset="0.6" stop-color="#f0a21c"/><stop offset="1" stop-color="#6b3a14"/>
      </radialGradient>
    </defs>
    <polygon points="0,0 321,0 366,50 0,50" fill="var(--blue)"/>
    <polygon points="0,50 366,50 371,55 0,55" fill="var(--green)"/>
    <polygon points="366,50 450,50 450,64 379,64" fill="url(#purpleFade)"/>
    <polygon points="418,52 490,12 526,60 495,88 450,78" fill="url(#shardsSmallB)" role="img" aria-label="Artwork: small cluster of overlapping triangles"/>
    <circle cx="456" cy="176" r="60" fill="none" stroke="var(--blue)" stroke-width="4"/>
    <circle cx="458" cy="176" r="55" fill="url(#climberPhoto)" role="img" aria-label="Photo: climber hanging from a rock overhang above golden clouds"/>
  </svg>
  <h2 class="slide-heading"><strong>ABOUT</strong> THE CHALLENGE</h2>
  <div class="accent-purple"></div>
  <p class="lead lead-wide" style="left:36px; top:73px; width:322px;">Lorem ipsum dolor sit amet, consectetuer adipiscing elit, sed diam nonummy nibh euismod tincidunt ut laoreet dolore magna aliquam erat volutpat. Ut wisi enim ad minim veniam,</p>
  <p class="body-small" style="left:17px; top:140px; width:356px;">Lorem ipsum dolor sit amet, consectetuer adipiscing elit, sed diam nonummy nibh euismod tincidunt ut laoreet dolore magna aliquam erat volutpat. Ut wisi enim ad minim veniam, Lorem ipsum dolor sit amet, Lorem ipsum dolor sit amet, consectetuer adipiscing elit, sed diam nonummy nibh euismod tincidunt ut laoreet dolore magna aliquam erat volutpat. Ut wisi enim ad minim veniam, quis nostrud exerci tation ullamcorper suscipit lobortis nisl ut aliquip ex ea</p>
  <ul class="bullets" style="left:17px; top:221px;">
    <li>Lorem ipsum dolor sit amet</li>
    <li>Lorem ipsum dolor sit amet</li>
    <li>Lorem ipsum dolor sit amet</li>
  </ul>
  <ul class="bullets" style="left:199px; top:221px;">
    <li>Lorem ipsum dolor sit amet</li>
    <li>Lorem ipsum dolor sit amet</li>
    <li>Lorem ipsum dolor sit amet</li>
  </ul>
  <div class="footer-url" style="left:19px; top:288px;">www.yourwebsite.com</div>
  <div class="footer-rule" style="left:66px; top:291px; width:430px;"></div>
  <div class="page-num" style="left:507px; top:286px;"><span>1</span></div>
</section>

</body>
</html>
```